Business Card Design for Translation Company - Rush

Rush job for a business card designing for a company doing international translations, several Asian and western languages. Already have a logo design (see attached) to use as the basis of the business card design. For the card, we also need the full company name, address, email, and phone number. In addition, my name as I will be the one handing out the cards.

For the logo design, we think the white background would be best. But we will consider using the dark background if you have a great idea for it.

The attached jpeg design has just been approved, but the designer has not yet finalized the file. When we select our final applicant, we will send the finalized file. (Nothing changes except the quality of the data.)

The phone number may change and if so, we will send the new one when we select our applicant.

We must complete the entire process and have a design ready to go to print no later than 01:00 am August 3, New York (East Coast) time.

We look forward to your participation in the project,
Dale

Target Market(s)

Translation clients worldwide.

Industry/Entity Type

Business

Contact Information for Business Card

Company details:

Korvanta Translations International, Ltd.

#207-2836 Wexholm Avenue, Victoria, BC, Canada V9T3K2

jquell@korvantatranslations.example

+1-888-604-7321

Font styles to use
Sans Serif

Requirements
Must have
• Company name, address, email and phone number.
• Also my name:
• Gordon R. Quell
• Director
Nice to have
• Not a demand, but please consider creatively using the horizontal bar.
Should not have
• Cluttered of jumbled appearance.

```html
<!DOCTYPE html>
<html lang="en">
<head>
<meta charset="utf-8">
<title>Korvanta Translations – Business Card</title>
<link rel="stylesheet" href="https://fonts.googleapis.com/css2?family=Lato:wght@300;400;700;900&display=swap">
<style>
  :root {
    --stage: #e9e6e1;
    --paper: #ffffff;
    --ink: #3d3d3d;
    --ink-soft: #555555;
    --accent: #f07d1a;
    --night: #1c1c1c;
    --night-edge: #2e2e2e;
    --ghost-peach: #fbe3cf;
  }
  * { box-sizing: border-box; margin: 0; padding: 0; }
  html, body {
    width: 1200px; height: 1024px; overflow: hidden;
    background: var(--stage);
    font-family: "Lato", Arial, sans-serif;
  }
  .sheet { position: relative; width: 1200px; height: 1024px; }
  .card {
    position: absolute; left: 250px; width: 700px; height: 400px;
    overflow: hidden; border-radius: 4px;
    box-shadow: 0 6px 18px rgba(0,0,0,0.18);
  }
  .card-front { top: 72px; background: var(--paper); }
  .card-back  { top: 552px; background: linear-gradient(135deg, var(--night) 0%, var(--night-edge) 100%); }

  /* Brand lockup: dot + stacked name, bar growing from a name line */
  .brand { position: absolute; display: flex; align-items: center; gap: 14px; }
  .brand-dot { flex: none; border-radius: 50%; background: var(--accent); }
  .brand-words { flex: 1; display: flex; flex-direction: column; gap: 4px; }
  .brand-line { display: flex; align-items: center; gap: 16px; }
  .brand-word { font-weight: 700; letter-spacing: 4px; white-space: nowrap; line-height: 1; }
  .brand-bar { flex: 1; height: 3px; background: var(--accent); }

  /* Front */
  .ghost-circle { position: absolute; left: -30px; bottom: -90px; }
  .card-front .brand { top: 44px; left: 48px; right: 48px; }
  .card-front .brand-dot { width: 30px; height: 30px; }
  .card-front .brand-word { font-size: 18px; color: var(--ink); }
  .contact {
    position: absolute; right: 48px; top: 132px; text-align: right; color: var(--ink);
  }
  .person-name { font-weight: 900; font-size: 19px; letter-spacing: 1px; text-transform: uppercase; }
  .person-rule { width: 190px; height: 2px; background: var(--accent); margin: 8px 0 6px auto; }
  .person-title { color: var(--accent); font-size: 14px; }
  .address { margin-top: 18px; font-size: 13px; line-height: 1.5; color: var(--ink-soft); }
  .lines { margin-top: 20px; font-size: 13px; line-height: 1.7; }
  .label { color: var(--accent); }

  /* Back */
  .card-back .brand { top: 150px; left: 90px; right: 90px; }
  .card-back .brand-dot { width: 34px; height: 34px; }
  .card-back .brand-word { font-size: 22px; color: #ffffff; }
  .website {
    position: absolute; top: 236px; left: 90px;
    color: var(--accent); font-size: 17px; letter-spacing: 0.5px;
  }
  .website .tld { color: #ffffff; }
</style>
</head>
<body>
<main class="sheet">
  <section class="card card-front" aria-label="Business card front">
    <svg class="ghost-circle" width="300" height="300" viewBox="0 0 300 300" aria-hidden="true">
      <circle cx="150" cy="150" r="140" fill="var(--ghost-peach)" opacity="0.6"/>
    </svg>
    <div class="brand">
      <span class="brand-dot"></span>
      <div class="brand-words">
        <div class="brand-line">
          <span class="brand-word">KORVANTA</span>
          <span class="brand-bar"></span>
        </div>
        <div class="brand-line">
          <span class="brand-word">TRANSLATIONS</span>
        </div>
      </div>
    </div>
    <div class="contact">
      <p class="person-name">Gordon R. Quell</p>
      <div class="person-rule"></div>
      <p class="person-title">Director</p>
      <p class="address">Korvanta Translations International, Ltd.<br>#207-2836 Wexholm Avenue, Victoria, BC<br>Canada V9T3K2</p>
      <p class="lines"><span class="label">Phone:</span> +1-888-604-7321<br><span class="label">E-mail:</span> jquell@korvantatranslations.example</p>
    </div>
  </section>

  <section class="card card-back" aria-label="Business card back">
    <div class="brand">
      <span class="brand-dot"></span>
      <div class="brand-words">
        <div class="brand-line">
          <span class="brand-word">KORVANTA</span>
        </div>
        <div class="brand-line">
          <span class="brand-word">TRANSLATIONS</span>
          <span class="brand-bar"></span>
        </div>
      </div>
    </div>
    <p class="website">www.korvantatranslations<span class="tld">.example</span></p>
  </section>
</main>
</body>
</html>
```